Fast-casual chicken restaurant Crisp Harbor needs a catering menu design

We need a catering menu designed for Crisp Harbor. We are looking to design a 24x36in landscape menu board for our new catering menu. The catering memo attached includes our catering menu and Crisp Harbor branding. More information about our brand can be found at https://crispharbor-eats.example/.

```html
<!DOCTYPE html>
<html lang="en">
<head>
<meta charset="utf-8">
<title>Crisp Harbor Catering Menu</title>
<link href="https://fonts.googleapis.com/css2?family=Montserrat:ital,wght@0,400;0,500;0,600;0,800;0,900;1,700&display=swap" rel="stylesheet">
<style>
:root{
  --sun:#fccd2b;
  --sun-shade:#f4c21f;
  --red:#d4392b;
  --white:#ffffff;
  --navy:#3b4a6e;
  --food-warm:#c9542a;
  --food-deep:#a63a1c;
  --plate:#f3f1ec;
}
*{margin:0;padding:0;box-sizing:border-box}
html,body{width:1200px;height:800px;overflow:hidden}
body{font-family:'Montserrat',sans-serif;background:var(--sun);position:relative}
.board{position:absolute;inset:0;width:1200px;height:800px;overflow:hidden}
.abs{position:absolute}
.food{position:absolute;border-radius:14px;background:radial-gradient(circle at 50% 50%,var(--food-warm) 0 55%,var(--food-deep) 75%,var(--plate) 76%)}
.food.fries{border-radius:0 0 50% 50%;background:radial-gradient(circle at 50% 20%,#e9a54a 0 60%,var(--plate) 62%)}
.food.bowl{border-radius:0 0 50% 0;background:radial-gradient(circle at 40% 30%,#b8863f 0 35%,var(--food-warm) 55%,var(--plate) 70%)}
.title{left:0;width:1200px;top:156px;text-align:center;font-weight:900;font-size:70px;letter-spacing:5px;color:var(--red);line-height:1;padding-left:10px}
.section-head{font-weight:900;font-size:25px;letter-spacing:3px;color:var(--white);line-height:1}
.rule{height:3px;background:var(--white)}
.note{left:140px;top:292px;font-size:10.5px;font-weight:700;font-style:italic;color:var(--navy);letter-spacing:.6px}
.pp-card{top:322px;width:142px;height:217px;background:var(--red);border-radius:3px;overflow:hidden;color:var(--white);text-align:center}
.pp-card .cap{position:relative;height:62px;background:var(--white);padding-top:12px}
.pp-card .cap::after{content:"";position:absolute;left:50%;bottom:-12px;margin-left:-14px;border-left:14px solid transparent;border-right:14px solid transparent;border-top:12px solid var(--white)}
.opt{font-size:9.5px;letter-spacing:1.6px;color:var(--red);font-weight:500}
.pp-card h3{font-size:23px;font-weight:900;color:var(--red);line-height:1;margin-top:1px}
.pp-card ul{list-style:none;font-size:13.5px;font-weight:500;line-height:15px;position:absolute;left:0;right:0}
.pp-card .price{position:absolute;bottom:12px;left:0;right:0;font-size:11.5px;letter-spacing:1.6px;font-weight:500}
.meal{top:308px;height:192px;width:160px;background:linear-gradient(90deg,var(--sun-shade),var(--sun) 80%)}
.meal::before{content:"";position:absolute;left:0;top:38px;border-top:18px solid transparent;border-bottom:18px solid transparent;border-left:16px solid var(--sun-shade);filter:brightness(.9)}
.meal .body{position:absolute;left:29px;top:8px}
.meal .opt{color:var(--red)}
.meal h3{font-size:26px;font-weight:900;color:var(--red);line-height:23px;margin-top:4px}
.meal ul{list-style:none;font-size:14px;font-weight:600;color:var(--red);line-height:15.3px;margin-top:4px}
.meal .price{position:absolute;left:29px;top:168px;font-size:12px;letter-spacing:1.6px;color:var(--red);font-weight:500}
.item{color:var(--red);line-height:1}
.item .name{font-size:20px;font-weight:900}
.item .cost{font-size:12px;font-weight:500;margin-top:2px}
.side .name{font-size:21px;font-weight:900;line-height:21px}
.side .size{font-size:12.5px;font-weight:500;margin-top:4px}
.side .cost{font-size:11.5px;letter-spacing:1.2px;font-weight:500}
.learn{left:708px;top:718px;width:418px;height:33px;border:3px solid var(--navy);border-radius:5px;background:var(--white);color:var(--navy);font-size:12.5px;letter-spacing:.3px;font-weight:500;white-space:nowrap;display:flex;align-items:center;justify-content:center;padding:0 14px 0 6px}
.learn b{font-weight:800;margin-left:4px}
.cursor{left:1116px;top:740px}
</style>
</head>
<body>
<main class="board">
  <div class="food bowl" style="left:-10px;top:-10px;width:268px;height:194px" role="img" aria-label="Bowl of glazed wings and breaded herb tenders"></div>
  <div class="food fries" style="left:272px;top:-10px;width:208px;height:82px" role="img" aria-label="Bowl of waffle fries"></div>
  <div class="food" style="left:504px;top:-10px;width:336px;height:134px" role="img" aria-label="Plate of buffalo sauced tenders"></div>
  <div class="food" style="left:880px;top:-10px;width:330px;height:182px" role="img" aria-label="Platter of glazed boneless wings"></div>
  <div class="food" style="left:-20px;top:168px;width:148px;height:296px" role="img" aria-label="Plate of barbecue wings"></div>

  <h1 class="abs title">CATERING MENU</h1>

  <h2 class="abs section-head" style="left:140px;top:265px">PER PERSON MEALS</h2>
  <div class="abs rule" style="left:470px;top:276px;width:126px"></div>
  <p class="abs note">&#9656; A MINIMUM OF 10 PEOPLE ARE NEEDED FOR THE PER PERSON DEALS</p>

  <section class="abs pp-card" style="left:140px">
    <div class="cap"><div class="opt">OPTION 1</div><h3>SNACK</h3></div>
    <ul style="top:98px"><li>2 TENDERS</li><li>SAUCE</li><li>DRESSING</li><li>1 REG SIDE</li></ul>
    <div class="price">$7.00/PERSON</div>
  </section>
  <section class="abs pp-card" style="left:296px">
    <div class="cap"><div class="opt">OPTION 2</div><h3>MEAL</h3></div>
    <ul style="top:98px"><li>2 TENDERS</li><li>3 WINGS</li><li>SAUCE</li><li>DRESSING</li><li>1 REG SIDE</li></ul>
    <div class="price">$11.00/PERSON</div>
  </section>
  <section class="abs pp-card" style="left:453px">
    <div class="cap"><div class="opt">OPTION 3</div><h3>FEAST</h3></div>
    <ul style="top:90px"><li>2 TENDERS</li><li>6 WINGS</li><li>SAUCE</li><li>DRESSING</li><li>1 REG SIDE</li><li>20OZ DRINK</li></ul>
    <div class="price">$15.00/PERSON</div>
  </section>

  <h2 class="abs section-head" style="left:630px;top:265px">MEALS</h2>
  <div class="abs rule" style="left:749px;top:276px;width:397px"></div>

  <section class="abs meal" style="left:632px">
    <div class="body"><div class="opt">OPTION 1</div><h3>FAMILY<br>MEAL</h3>
    <ul><li>12 TENDERS</li><li>LARGE SIDE</li><li>2L BEVERAGE</li></ul></div>
    <div class="price">$24.99</div>
  </section>
  <section class="abs meal" style="left:794px;width:172px">
    <div class="body"><div class="opt">OPTION 2</div><h3>PARTY<br>PACK</h3>
    <ul><li>20 TENDERS</li><li>30 WINGS</li><li>2 TRAY SIDES</li><li>1 - 2L BEVERAGE</li></ul></div>
    <div class="price">$75.99</div>
  </section>
  <section class="abs meal" style="left:966px;width:180px">
    <div class="body"><div class="opt">OPTION 3</div><h3>AIRCRAFT<br>CARRIER</h3>
    <ul><li>20 TENDERS</li><li>60 WINGS</li><li>4 TRAY SIDES</li><li>2 - 2L BEVERAGE</li></ul></div>
    <div class="price" style="top:166px">$155.99</div>
  </section>

  <h2 class="abs section-head" style="left:98px;top:565px">WINGS</h2>
  <div class="abs rule" style="left:218px;top:576px;width:62px"></div>
  <h2 class="abs section-head" style="left:294px;top:565px">TENDERS</h2>
  <div class="abs rule" style="left:445px;top:576px;width:87px"></div>
  <h2 class="abs section-head" style="left:546px;top:565px">SIDES</h2>
  <div class="abs rule" style="left:650px;top:576px;width:496px"></div>

  <div class="abs item" style="left:104px;top:607px"><div class="name">50 WINGS</div><div class="cost">$7.00</div></div>
  <div class="abs item" style="left:104px;top:655px"><div class="name">75 WINGS</div><div class="cost">$XX.XX</div></div>
  <div class="abs item" style="left:104px;top:700px"><div class="name">100 WINGS</div><div class="cost">$XX.XX</div></div>
  <div class="abs item" style="left:296px;top:607px"><div class="name">30 TENDERS</div><div class="cost">$7.00</div></div>
  <div class="abs item" style="left:296px;top:655px"><div class="name">45 TENDERS</div><div class="cost">$XX.XX</div></div>
  <div class="abs item" style="left:296px;top:700px"><div class="name">60 TENDERS</div><div class="cost">$XX.XX</div></div>

  <div class="abs item side" style="left:554px;top:607px"><div class="name">WAFFLE<br>FRIES</div><div class="size">PARTY SIZE</div><div class="cost">$13.99</div></div>
  <div class="abs item side" style="left:718px;top:607px"><div class="name">GARLIC<br>PARM<br>TOTS</div><div class="size">PARTY SIZE</div><div class="cost">$13.99</div></div>
  <div class="abs item side" style="left:873px;top:607px"><div class="name">CHICKEN<br>CAESAR<br>SALAD</div><div class="size">PARTY SIZE</div><div class="cost">$38.99</div></div>
  <div class="abs item side" style="left:1049px;top:607px"><div class="name">CAESAR<br>SALAD</div><div class="size">PARTY SIZE</div><div class="cost">$27.99</div></div>

  <div class="abs learn">LEARN MORE AT <b>CRISPHARBOR-EATS.EXAMPLE/MENU</b></div>
  <svg class="abs cursor" width="34" height="34" viewBox="0 0 34 34" aria-hidden="true">
    <g stroke="var(--red)" stroke-width="2" stroke-linecap="round">
      <line x1="6" y1="2" x2="6" y2="6"/><line x1="1" y1="7" x2="4" y2="7"/><line x1="2" y1="2" x2="4" y2="4"/>
    </g>
    <path d="M9 9 L27 16 L19 19 L27 27 L24 30 L16 22 L13 29 Z" fill="var(--white)" stroke="var(--red)" stroke-width="2" stroke-linejoin="round"/>
  </svg>
</main>
</body>
</html>
```